All-Natural Head Lice Removal company

I need a business card with my pre-existing logo. We are a new company located in Portland Oregon that goes into peoples homes to help with head lice removal. My products and approach are all- natural and also will be around children.On my current logo we used Teal Bl and the color Green. I am open to new ideas just want it simple and creative

Target Market(s)

my biggest market is families of school aged children

Industry/Entity Type

Business

Contact Information for Business Card

see upload for details from previous business card

Font styles to use
Serif

Colors
33a6d7
9bcb3b
f37122

Requirements
Must have
• Basic information/ logo put into a creative format that is catching to the eye
Nice to have
• creative

```html
<!DOCTYPE html>
<html lang="en">
<head>
<meta charset="utf-8">
<title>Clear Crown Business Card</title>
<link rel="stylesheet" href="https://fonts.googleapis.com/css2?family=Roboto+Slab:wght@400;700&family=Open+Sans:wght@400;600&display=swap">
<style>
  :root {
    --bg: #e9e6e1;
    --green: #8fcf4a;
    --teal: #33a6d7;
    --ink: #2b2b2b;
    --white: #ffffff;
    --black: #111111;
    --black-soft: #2e2e2e;
  }
  html, body {
    margin: 0;
    width: 1200px;
    height: 913px;
    overflow: hidden;
    background: var(--bg);
  }
  .canvas {
    position: relative;
    width: 1200px;
    height: 913px;
  }
  .card {
    position: absolute;
    top: 302px;
    width: 540px;
    height: 309px;
    border-radius: 18px;
    overflow: hidden;
    box-shadow: 0 6px 18px rgba(0,0,0,0.18);
  }
  .card-front { left: 40px; background: var(--white); }
  .card-back {
    left: 620px;
    background: linear-gradient(160deg, var(--black-soft) 0%, var(--black) 60%);
  }
  .front-shape { position: absolute; inset: 0; }
  .holder {
    position: absolute;
    left: 34px;
    top: 132px;
  }
  .holder-name {
    font: 700 21px/1 "Roboto Slab", serif;
    color: var(--ink);
    letter-spacing: 0.5px;
    margin: 0;
  }
  .holder-role {
    font: 400 13px/1 "Open Sans", sans-serif;
    color: var(--teal);
    letter-spacing: 1px;
    margin: 6px 0 0;
  }
  .contact-list {
    position: absolute;
    left: 34px;
    top: 206px;
    margin: 0;
    padding: 0;
    list-style: none;
    font: 600 14px/1 "Open Sans", sans-serif;
    color: var(--ink);
  }
  .contact-list li {
    display: flex;
    align-items: center;
    gap: 8px;
    margin-bottom: 7px;
  }
  .contact-list svg { width: 12px; height: 12px; flex: none; }
  .brand {
    display: flex;
    align-items: center;
    justify-content: center;
    gap: 8px;
    font: 700 26px/1 "Roboto Slab", serif;
    color: var(--ink);
    white-space: nowrap;
  }
  .brand-dot {
    width: 20px;
    height: 20px;
    border-radius: 50%;
    background: var(--teal);
  }
  .front-brand {
    position: absolute;
    right: 28px;
    top: 36px;
    width: 210px;
    text-align: center;
  }
  .front-tagline {
    font: 400 12px/1.35 "Roboto Slab", serif;
    color: var(--ink);
    margin: 10px 0 0;
  }
  .back-content {
    position: absolute;
    inset: 0;
    display: flex;
    flex-direction: column;
    align-items: center;
    justify-content: center;
    text-align: center;
  }
  .back-emblem {
    width: 150px;
    height: 150px;
    border-radius: 50%;
    background: var(--green);
    display: flex;
    align-items: center;
    justify-content: center;
  }
  .back-emblem .brand { color: var(--black); font-size: 20px; }
  .back-tagline {
    font: 400 14px/1.35 "Roboto Slab", serif;
    color: var(--white);
    margin: 16px 0 6px;
  }
  .back-url {
    font: 400 14px/1 "Roboto Slab", serif;
    color: var(--teal);
    margin: 0;
  }
</style>
</head>
<body>
<main class="canvas">
  <section class="card card-front">
    <svg class="front-shape" viewBox="0 0 540 309" aria-hidden="true">
      <defs>
        <linearGradient id="greenFill" x1="0" y1="0" x2="1" y2="1">
          <stop offset="0" stop-color="#b4e27a"/>
          <stop offset="1" stop-color="#7dc23a"/>
        </linearGradient>
      </defs>
      <path d="M0,70 C220,70 440,150 470,309 L540,309 L540,0 L0,0 Z" fill="url(#greenFill)"/>
      <path d="M0,70 C220,70 440,150 470,309" fill="none" stroke="#33a6d7" stroke-width="3"/>
      <path d="M0,63 C224,63 448,144 479,309" fill="none" stroke="#ffffff" stroke-width="2" stroke-opacity="0.6"/>
    </svg>
    <div class="holder">
      <p class="holder-name">DANA WHITFIELD</p>
      <p class="holder-role">OWNER</p>
    </div>
    <ul class="contact-list">
      <li><svg viewBox="0 0 12 12"><path d="M3 1 L5 3.5 L4 5 Q5.5 7 7 8 L8.5 7 L11 9 L9.5 11 Q4 10 1 2.5 Z" fill="#33a6d7"/></svg>1-800-555-NITS (6487)</li>
      <li><svg viewBox="0 0 12 12"><rect x="1" y="2.5" width="10" height="7" fill="none" stroke="#33a6d7" stroke-width="1.4"/><path d="M1 2.5 L6 6.5 L11 2.5" fill="none" stroke="#33a6d7" stroke-width="1.4"/></svg>Dana@ClearCrown.com</li>
      <li><svg viewBox="0 0 12 12"><circle cx="6" cy="6" r="5" fill="#33a6d7"/><path d="M1 6 H11 M6 1 V11" stroke="#fff" stroke-width="1"/></svg>www.ClearCrown.com</li>
    </ul>
    <div class="front-brand">
      <div class="brand"><span class="brand-dot"></span>Clear Crown</div>
      <p class="front-tagline">All Natural In-Home<br>Lice Removal Services</p>
    </div>
  </section>

  <section class="card card-back">
    <div class="back-content">
      <div class="back-emblem">
        <div class="brand">Clear Crown</div>
      </div>
      <p class="back-tagline">Try Clear Crown Today and Be Lice Free Tomorrow!<br>All Natural In-Home Lice Removal Services</p>
      <p class="back-url">www.ClearCrown.com</p>
    </div>
  </section>
</main>
</body>
</html>
```